Help design website for "Brightwater Civic Advisors" to advance the common good

Here is the Google doc link that lays out the design:

https://files.plumrivet.example/sheet/d/7QmTzR2wLx9KpVbN4hJcY8sEaUoFdG3iXkMnPq5rWt6/edit?usp=sharing

Here is the Google drive folder with the logos and photos: https://vault.plumrivet.example/open?id=4HkWp9LzQe2TxRvN8mBaYc3DsUoJfG6

The testimonials are being gathered and will be shared by Friday, 1/4.

The winner will also have to migrate the coding files to my hosting site.

Thank you for your help! Looking forward to seeing your designs.

Target Market(s)

Prospective clients

Industry/Entity Type

Non Profit

Coding

Coded - Design and coding required

Number of Pages Required

5+ page

Requirements
Must have
• Noted in the Google doc regarding layout.
Nice to have

```html
<!DOCTYPE html>
<html lang="en">
<head>
<meta charset="utf-8">
<title>Brightwater Civic Advisors</title>
<link href="https://fonts.googleapis.com/css2?family=Montserrat:wght@400;500;600;700&family=Poppins:wght@400;500;600&display=swap" rel="stylesheet">
<style>
:root{
  --blue:#3d8fd6;
  --blue-tile:rgba(61,143,214,.92);
  --ink:#333640;
  --text:#55585f;
  --muted:#7a7d84;
  --band:#f1f1f1;
  --footer:#2f323d;
  --white:#ffffff;
  --star:#f39a1f;
}
*{box-sizing:border-box;margin:0;padding:0}
html,body{width:1200px;height:3711px;overflow:hidden;background:var(--white)}
body{font-family:"Poppins",sans-serif;color:var(--text)}
.page{position:relative;width:1200px;height:3711px;overflow:hidden}
h2.section-title{position:absolute;left:0;width:1200px;text-align:center;font-family:"Montserrat",sans-serif;font-weight:500;font-size:46px;color:var(--blue)}

/* hero */
.hero{position:absolute;left:0;top:0;width:1200px;height:643px;
  background:
    radial-gradient(ellipse 520px 240px at 600px 470px,rgba(120,80,70,.55),transparent 70%),
    radial-gradient(ellipse 400px 200px at 180px 420px,rgba(150,110,95,.45),transparent 70%),
    radial-gradient(ellipse 400px 200px at 1020px 420px,rgba(110,95,110,.45),transparent 70%),
    linear-gradient(180deg,#d3e1ea 0%,#a9c3d6 14%,#7f9fb5 24%,#5c6f7c 36%,#5a5450 55%,#4c4a44 72%,#4a6640 88%,#3b5631 100%)}
.hero-shape{position:absolute;left:0;top:540px}
.nav{position:absolute;left:113px;top:40px;display:flex;gap:22px;font-family:"Montserrat",sans-serif;font-size:15px;font-weight:500;color:var(--ink)}
.nav .active{color:var(--blue)}
.brand{position:absolute;left:770px;top:44px;display:flex;align-items:center;gap:12px;font-family:"Montserrat",sans-serif;font-weight:600;font-size:22px;color:#2e3a48;letter-spacing:.5px}
.brand-square{width:34px;height:34px;background:var(--blue)}
.hero-kicker{position:absolute;left:0;top:198px;width:1200px;text-align:center;font-family:"Montserrat",sans-serif;font-weight:600;font-size:46px;color:var(--white)}
.hero-title{position:absolute;left:0;top:262px;width:1200px;text-align:center;font-family:"Montserrat",sans-serif;font-weight:600;font-size:60px;color:var(--white)}
.hero-lead{position:absolute;left:290px;top:350px;width:620px;text-align:center;font-size:19px;line-height:30px;font-weight:500;color:var(--white)}
.btn-solid{position:absolute;background:var(--blue);color:var(--white);border-radius:30px;font-family:"Montserrat",sans-serif;font-weight:500;display:flex;align-items:center;justify-content:center}
.slider-dots{position:absolute;left:1142px;top:290px;display:flex;flex-direction:column;gap:12px;align-items:center}
.slider-dots span{width:9px;height:9px;border-radius:50%;background:var(--white)}
.slider-dots .on{width:18px;height:18px;border:2px solid var(--white);background:transparent}

/* about */
.about-photo{position:absolute;left:111px;top:712px;width:390px;height:377px;
  background:radial-gradient(ellipse 150px 170px at 200px 210px,#a07a62,transparent 75%),
  linear-gradient(160deg,#8a8580,#55504a 45%,#2a2724);box-shadow:0 4px 12px rgba(0,0,0,.25)}
.about-title{position:absolute;left:559px;top:708px;font-family:"Montserrat",sans-serif;font-weight:500;font-size:44px;color:var(--blue)}
.about-copy{position:absolute;left:559px;top:775px;width:530px;font-size:13.4px;line-height:22px;color:var(--text)}
.about-copy p{margin-bottom:12px}
.btn-outline{position:absolute;left:554px;top:1039px;width:182px;height:50px;border:2px solid var(--blue);border-radius:26px;color:var(--ink);font-family:"Montserrat",sans-serif;font-weight:500;font-size:17px;display:flex;align-items:center;justify-content:center}

/* services */
.tile{position:absolute;overflow:hidden}
.tile-label{position:absolute;right:0;bottom:0;background:var(--blue-tile);color:var(--white);font-family:"Montserrat",sans-serif;font-weight:600;font-size:17px;line-height:20px;padding:0 14px 0 18px;display:flex;align-items:center}

/* testimonials */
.band{position:absolute;left:0;top:1838px;width:1200px;height:586px;background:var(--band)}
.card{position:absolute;top:2036px;height:175px;background:var(--white);border-radius:10px;box-shadow:0 2px 10px rgba(0,0,0,.12);text-align:center;font-size:13.4px;line-height:24px;color:var(--text);padding:54px 20px 0}
.card::after{content:"";position:absolute;left:50%;bottom:-12px;margin-left:-12px;border-left:12px solid transparent;border-right:12px solid transparent;border-top:12px solid var(--white)}
.avatar{position:absolute;top:1988px;width:90px;height:90px;border-radius:50%;border:4px solid var(--white);box-shadow:0 2px 6px rgba(0,0,0,.2)}
.person{position:absolute;top:2260px;text-align:center;font-size:14px;line-height:21px;color:var(--ink)}
.person .name{color:var(--blue);font-size:15px;margin-bottom:3px}
.person svg{display:block;margin:8px auto 0}

/* media */
.media-img{position:absolute;top:2580px;width:300px;height:203px}
.media-icon{position:absolute;left:14px;top:14px;width:36px;height:36px;border:2px solid var(--white);border-radius:6px;background:rgba(255,255,255,.15)}
.media-cap{position:absolute;top:2800px;width:300px;text-align:center}
.media-cap h3{font-family:"Montserrat",sans-serif;font-weight:600;font-size:20px;color:var(--blue);margin-bottom:12px}
.media-cap p{font-size:14px;line-height:24px;color:var(--text)}

/* footer */
.footer-shape{position:absolute;left:0;top:2940px}
.footer-badge{position:absolute;left:494px;top:2942px;width:212px;height:212px;border-radius:50%;background:var(--white);box-shadow:0 2px 8px rgba(0,0,0,.25);display:flex;align-items:center;justify-content:center;text-align:center;font-family:"Montserrat",sans-serif;font-weight:600;font-size:19px;line-height:26px;color:var(--blue);padding:0 30px}
.map{position:absolute;left:116px;top:3209px;width:418px;height:373px;
  background:radial-gradient(ellipse 120px 90px at 120px 120px,#cfe0c2,transparent 75%),
  radial-gradient(ellipse 140px 90px at 320px 280px,#d4e3c8,transparent 75%),
  linear-gradient(135deg,#ece8dd,#e0e2d6 45%,#ece7de)}
.contact{position:absolute;color:var(--white);font-size:14px;line-height:21px;display:flex;gap:16px;align-items:flex-start}
.field{position:absolute;border:1px solid #8a8d96;background:var(--white);color:var(--muted);font-size:13.5px;padding:12px 16px}
.social{position:absolute;left:536px;top:3632px;display:flex;gap:10px}
.social span{width:24px;height:24px;border-radius:50%;border:2px solid #d7d8dc}
.copyright{position:absolute;left:0;top:3672px;width:1200px;text-align:center;color:var(--white);font-size:13.5px}
</style>
</head>
<body>
<div class="page">

  <svg width="0" height="0" style="position:absolute" aria-hidden="true"><defs><polygon id="st" points="9,1 11.3,6.5 17,7 12.7,10.8 14,16.5 9,13.5 4,16.5 5.3,10.8 1,7 6.7,6.5"/></defs></svg>

  <!-- Hero -->
  <section class="hero" role="img" aria-label="Group of people cheering on a lakeside with city skyline behind"></section>
  <svg class="hero-shape" width="1200" height="110" viewBox="0 0 1200 110" aria-hidden="true">
    <polygon points="0,103 600,10 1200,103 1200,110 0,110" fill="#ffffff"/>
    <polyline points="0,103 600,10 1200,103" fill="none" stroke="#3d8fd6" stroke-width="5"/>
  </svg>
  <nav class="nav">
    <span class="active">Home</span><span>About</span><span>Services &amp; Testimonials</span><span>Media &amp; Impact</span><span>Contact</span>
  </nav>
  <div class="brand"><span class="brand-square"></span>Brightwater Civic Advisors</div>
  <div class="hero-kicker">Welcome To</div>
  <h1 class="hero-title">Brightwater Civic Advisors</h1>
  <p class="hero-lead">Lorem ipsum dolor sit amet, consectetur adipiscing elit, sed do eiusmod tempor incididunt ut labore et</p>
  <div class="btn-solid" style="left:507px;top:428px;width:188px;height:49px;font-size:18px">Read More</div>
  <div class="slider-dots"><span class="on"></span><span></span><span></span></div>

  <!-- About -->
  <div class="about-photo" role="img" aria-label="Portrait of the firm's founder"></div>
  <h2 class="about-title">About Us</h2>
  <div class="about-copy">
    <p>Brightwater Civic Advisors supports nonprofit organizations and educational institutions to carry out their missions to benefit the wider community.</p>
    <p>Founder Lena Park is an educator with a 22-year record of demonstrated achievement and leadership roles in nonprofits and educational institutions. Most recently, she served as Associate Dean of Students in the University and Director of the University Community Service Center at Lakeshore University. Lena has designed, implemented, and evaluated community-based learning and leadership training programs that have attained positive outcomes documented by survey results, recognition by outside agencies, and grants awarded for new initiatives and expansions.</p>
  </div>
  <div class="btn-outline">Read More</div>

  <!-- Services -->
  <h2 class="section-title" style="top:1200px">Our Services</h2>
  <div class="tile" style="left:0;top:1304px;width:364px;height:205px;background:radial-gradient(ellipse 200px 90px at 180px 110px,#a5806a,transparent 75%),linear-gradient(150deg,#9a8474,#5a4538 60%,#3e302a)" role="img" aria-label="Staff workshop group photo">
    <div class="tile-label" style="width:228px;height:52px">Staff Professional<br>Development</div></div>
  <div class="tile" style="left:376px;top:1304px;width:450px;height:259px;background:radial-gradient(ellipse 240px 110px at 220px 170px,#8e6a58,transparent 75%),linear-gradient(160deg,#b3aba1,#6e6a65 50%,#3a3838)" role="img" aria-label="Students from a community partnership program">
    <div class="tile-label" style="width:270px;height:58px">Community Partnership<br>Development</div></div>
  <div class="tile" style="left:839px;top:1304px;width:361px;height:205px;background:radial-gradient(ellipse 160px 80px at 120px 60px,#c98a5c,transparent 75%),linear-gradient(150deg,#b27a55,#6c5244 55%,#48403c)" role="img" aria-label="Group facilitation session in a classroom">
    <div class="tile-label" style="width:228px;height:52px">Group Facilitation<br>&amp; Leadership Training</div></div>
  <div class="tile" style="left:0;top:1524px;width:364px;height:257px;background:radial-gradient(ellipse 220px 110px at 180px 170px,#7a5d56,transparent 75%),linear-gradient(170deg,#a3c0d4,#6a8294 35%,#4b5340)" role="img" aria-label="Program participants celebrating outdoors">
    <div class="tile-label" style="width:228px;height:58px">Program Design,<br>Implementation</div></div>
  <div class="tile" style="left:376px;top:1576px;width:450px;height:205px;background:radial-gradient(ellipse 160px 90px at 280px 110px,#c69a7a,transparent 75%),linear-gradient(150deg,#a0724e,#6d4b35 55%,#4a3629)" role="img" aria-label="Event set-up in a hall">
    <div class="tile-label" style="width:270px;height:52px">Event Planning</div></div>
  <div class="tile" style="left:839px;top:1524px;width:361px;height:257px;background:radial-gradient(ellipse 140px 100px at 130px 90px,#e9ebef,transparent 75%),linear-gradient(150deg,#c9ccd2,#8f9199 50%,#565860)" role="img" aria-label="Presenter beside a projected strategy slide">
    <div class="tile-label" style="width:228px;height:58px">Strategic Planning<br>&amp; Visioning</div></div>

  <!-- Testimonials -->
  <div class="band"></div>
  <h2 class="section-title" style="top:1893px">Testimonials</h2>

  <div class="card" style="left:119px;width:292px">Lorem ipsum dolor sit amet, consectetur adipiscing elit, sed do eiusmod tempor incididunt ut labore et dolore magna aliqua.</div>
  <div class="avatar" style="left:220px;background:linear-gradient(150deg,#a77d67,#5b4033)" role="img" aria-label="Client portrait"></div>
  <div class="card" style="left:453px;width:292px">Lorem ipsum dolor sit amet, consectetur adipiscing elit, sed do eiusmod tempor incididunt ut labore et dolore magna aliqua.</div>
  <div class="avatar" style="left:554px;background:linear-gradient(150deg,#b88565,#6a4432)" role="img" aria-label="Client portrait"></div>
  <div class="card" style="left:787px;width:292px">Lorem ipsum dolor sit amet, consectetur adipiscing elit, sed do eiusmod tempor incididunt ut labore et dolore magna aliqua.</div>
  <div class="avatar" style="left:888px;background:linear-gradient(150deg,#9ea5ab,#4f5a63)" role="img" aria-label="Client portrait"></div>

  <div class="person" style="left:89px;width:352px">
    <div class="name">Marisol Vance</div>Executive Director,<br>Lanternway Community Development
    <svg width="110" height="18" viewBox="0 0 110 18" aria-hidden="true"><g fill="#f39a1f"><use href="#st"/><use href="#st" x="22"/><use href="#st" x="44"/><use href="#st" x="66"/><use href="#st" x="88"/></g></svg>
  </div>
  <div class="person" style="left:433px;width:332px">
    <div class="name">Dov Hartley</div>Chief Operations &amp; Growth Officer,<br>Open Horizon
    <svg width="110" height="18" viewBox="0 0 110 18" aria-hidden="true"><g fill="#f39a1f"><use href="#st"/><use href="#st" x="22"/><use href="#st" x="44"/><use href="#st" x="66"/><use href="#st" x="88"/></g></svg>
  </div>
  <div class="person" style="left:787px;width:292px">
    <div class="name">Theo Okafor</div>Chief Executive Officer,<br>Fairbridge Forum
    <svg width="110" height="18" viewBox="0 0 110 18" aria-hidden="true"><g fill="#f39a1f"><use href="#st"/><use href="#st" x="22"/><use href="#st" x="44"/><use href="#st" x="66"/><use href="#st" x="88"/></g></svg>
  </div>

  <!-- Media & Impact -->
  <h2 class="section-title" style="top:2490px">Media &amp; Impact</h2>
  <div class="media-img" style="left:116px;background:radial-gradient(ellipse 150px 60px at 150px 130px,#a8a099,transparent 75%),linear-gradient(150deg,#8b7a68,#4d4238 55%,#2f2925)" role="img" aria-label="Community meeting in a hall">
    <div class="media-icon"></div></div>
  <div class="media-img" style="left:440px;background:radial-gradient(ellipse 130px 70px at 160px 60px,#dfe2dc,transparent 75%),linear-gradient(170deg,#c3c6c0,#7b8a6f 50%,#3f5a32)" role="img" aria-label="Group touring a campus lawn">
    <svg class="media-icon" viewBox="0 0 36 36" aria-hidden="true" style="border-radius:50%"><polygon points="13,10 25,17 13,24" fill="#fff"/></svg></div>
  <div class="media-img" style="left:764px;background:radial-gradient(ellipse 90px 90px at 150px 110px,#8a6a58,transparent 75%),linear-gradient(150deg,#4a3a30,#2a211c 55%,#171310)" role="img" aria-label="Speaker at a podium">
    <div class="media-icon"></div></div>

  <div class="media-cap" style="left:116px"><h3>Lorem ipsum dolor sit</h3><p>At vero eos et accusamus et iusto<br>odio dignissimos ducimus</p></div>
  <div class="media-cap" style="left:440px"><h3>Lorem ipsum dolor sit</h3><p>At vero eos et accusamus et iusto<br>odio dignissimos ducimus</p></div>
  <div class="media-cap" style="left:764px"><h3>Lorem ipsum dolor sit</h3><p>At vero eos et accusamus et iusto<br>odio dignissimos ducimus</p></div>

  <!-- Footer -->
  <svg class="footer-shape" width="1200" height="771" viewBox="0 0 1200 771" aria-hidden="true">
    <polygon points="0,9 600,82 1200,9 1200,771 0,771" fill="#2f323d"/>
    <polyline points="0,9 600,82 1200,9" fill="none" stroke="#3d8fd6" stroke-width="5"/>
  </svg>
  <div class="footer-badge">Brightwater Civic Advisors</div>

  <div class="map" role="img" aria-label="Street map showing the office location"></div>

  <div class="contact" style="left:585px;top:3206px">
    <svg width="18" height="22" viewBox="0 0 18 22" aria-hidden="true"><path d="M9 1a7 7 0 0 1 7 7c0 5-7 13-7 13S2 13 2 8a7 7 0 0 1 7-7z" fill="#fff"/><circle cx="9" cy="8" r="2.6" fill="#2f323d"/></svg>
    <div>Harbor Street, District IV, 4420 Calder Bay,<br>Easton Province</div>
  </div>
  <div class="contact" style="left:585px;top:3263px">
    <svg width="18" height="18" viewBox="0 0 18 18" aria-hidden="true"><path d="M4 1l3 4-2 2c1 2 3 4 5 5l2-2 4 3-2 3C8 16 2 10 1 4z" fill="#fff"/></svg>
    <div>(555) 014 2290</div>
  </div>
  <div class="contact" style="left:780px;top:3263px">
    <svg width="20" height="16" viewBox="0 0 20 16" aria-hidden="true"><rect x="1" y="2" width="18" height="12" fill="#fff"/><polyline points="1,2 10,9 19,2" fill="none" stroke="#2f323d" stroke-width="1.6"/></svg>
    <div>info@brightwatercivic.example</div>
  </div>

  <div class="field" style="left:589px;top:3315px;width:245px;height:50px">First Name</div>
  <div class="field" style="left:844px;top:3315px;width:242px;height:50px">Last Name</div>
  <div class="field" style="left:589px;top:3372px;width:245px;height:50px">Email</div>
  <div class="field" style="left:844px;top:3372px;width:242px;height:50px">Phone Number</div>
  <div class="field" style="left:589px;top:3427px;width:497px;height:91px">Message</div>
  <div class="btn-solid" style="left:586px;top:3540px;width:139px;height:40px;font-size:16px">Submit</div>

  <div class="social" aria-hidden="true"><span></span><span></span><span></span><span></span></div>
  <div class="copyright">© 2018 Copyrights | All Rights Reserved</div>
</div>
</body>
</html>
```